UX Design for Analytics Web Application

http://velqoranthe.com/
We are tech & consulting company with analytics products (web applications), located at Rio de Janeiro, Brazil.

We are searching a partner do develop UX for our products, i.e, aesthetics, usability, HTML/CSS.

Currently we have a product suite and the goal is to make a pilot re-design project with one of our products.

The product of interest is interactive webapp that aims at data analysis, significantly different from blogs, e-commerce or landing pages.

We do have a software development team but we lack an UX & HTML expert. Currently we use Bootstrap templates but the results are insatisfatory.

So, the project scope is, to develop the arts (UX, aesthetics, etc) along with the code/mockup (HTML/CSS) for one of our product (3 pages).

This is a pilot project and there's potential to rehire for our other products. Code quality is of importance.

More details and specification can be found in attached files.

Target Market(s)

Executives, managers & consultants

Industry/Entity Type

It Company

Coding

Coded - Design and coding required

Number of Pages Required

3 page

Font styles to use
Sans Serif

Requirements
Must have
• (see attached files, prefer the pptx version))
• -Responsive
Nice to have
• (see attached files, prefer the pptx version)
Should not have
• -Avoid Green, Red and Yellow colors. They have a meaning of good, bad and average in our products.

```html
<!DOCTYPE html>
<html lang="en">
<head>
<meta charset="utf-8">
<title>Velqora Dashboard</title>
<link href="https://fonts.googleapis.com/css2?family=Poppins:wght@300;400;500;600;700&display=swap" rel="stylesheet">
<style>
:root{
  --tone-blue:#2f6db5;
  --tone-violet:#5a4aa6;
  --tone-navy:#1f3f66;
  --hero-sky:#8cc4ff;
  --hero-lilac:#c3b5ff;
  --hero-ice:#b8e4ff;
  --ink:#3a3a3a;
  --muted:#555;
  --white:#fff;
}
*{box-sizing:border-box;margin:0;padding:0}
html,body{width:902px;height:1200px;overflow:hidden;background:var(--white);font-family:'Poppins',sans-serif;color:var(--ink)}
.page{position:relative;width:902px;height:1200px}

.topbar{position:absolute;left:0;top:0;width:902px;height:78px;background:var(--white)}
.menu-toggle{position:absolute;left:108px;top:29px}
.brand{position:absolute;left:158px;top:20px;display:flex;align-items:center;gap:7px}
.brand-mark{width:22px;height:22px;border-radius:50%;border:3px solid var(--ink)}
.brand-name{font-size:24px;font-weight:600;color:var(--ink);letter-spacing:-.5px}
.nav-item{display:flex;align-items:center;gap:6px;font-size:12.5px;color:var(--muted);position:absolute;white-space:nowrap}
.nav-item svg{width:16px;height:16px}

.hero{position:absolute;left:0;top:78px;width:902px;height:410px;
  background:radial-gradient(ellipse at 30% 35%,#77767a 0%,#5b5a5e 30%,#3d3b3d 65%,#2b2827 100%)}
.stat{position:absolute;top:150px;width:130px;margin-left:-65px;text-align:center;color:var(--white)}
.stat-value{font-size:38px;font-weight:300;line-height:1;height:46px}
.stat-label{font-size:16px;font-weight:500;line-height:1.2;margin-top:20px}
.stat-divider{position:absolute;top:154px;width:1px;height:124px;background:rgba(255,255,255,.7)}
.stat.feed{width:96px;margin-left:-48px;top:146px}
.avatar{width:60px;height:60px;border-radius:50%;background:linear-gradient(#d9d3cc,#a48a72);border:2px solid #fff;margin:0 auto}
.feed-name{font-size:9.5px;font-weight:600;margin-top:6px}
.feed-date{font-size:7.5px;color:var(--hero-sky);margin-top:6px}
.slider-dots{position:absolute;top:381px;left:421px;display:flex;gap:11px}
.slider-dots span{width:6px;height:6px;border-radius:50%;background:#fff}
.slider-dots span.active{background:var(--hero-sky)}

.card{position:absolute;width:217px;height:260px;color:var(--white);text-align:center;box-shadow:3px 4px 0 #eeeeee}
.card.blue{background:var(--tone-blue)}
.card.violet{background:var(--tone-violet)}
.card.navy{background:var(--tone-navy)}
.card-title{position:absolute;top:40px;left:0;right:0;font-size:14.5px;font-weight:600}
.card-rule{position:absolute;top:87px;left:50%;width:52px;margin-left:-26px;height:2px;background:rgba(0,0,0,.3)}
.card-heading{position:absolute;top:113px;left:0;right:0;font-size:24px;font-weight:700;line-height:1}
.card-value{position:absolute;top:196px;left:0;right:0;font-size:20px;font-weight:300}
.card-text{position:absolute;top:188px;left:28px;right:28px;font-size:11.5px;line-height:1.35}
.card-count{position:absolute;top:183px;left:0;right:0;font-size:30px;font-weight:700}

.footer{position:absolute;left:0;top:1142px;width:902px;border-top:1px solid #f0f0f0;height:58px}
.footer p{position:absolute;top:23px;left:0;right:0;text-align:center;font-size:12px;color:var(--muted)}
</style>
</head>
<body>
<div class="page">
  <header class="topbar">
    <svg class="menu-toggle" width="21" height="18" viewBox="0 0 21 18"><rect y="0" width="21" height="3.5" fill="#666"/><rect y="7" width="21" height="3.5" fill="#666"/><rect y="14" width="21" height="3.5" fill="#666"/></svg>
    <div class="brand"><span class="brand-mark"></span><span class="brand-name">Velqora</span></div>
    <nav>
      <span class="nav-item" style="left:480px;top:33px">
        <svg viewBox="0 0 16 16"><circle cx="8" cy="7" r="4" fill="none" stroke="#2f6db5" stroke-width="1.2"/><rect x="6.5" y="11" width="3" height="2.5" fill="#2f6db5"/><g stroke="#2f6db5" stroke-width="1"><line x1="8" y1="0.5" x2="8" y2="2"/><line x1="1" y1="7" x2="2.5" y2="7"/><line x1="13.5" y1="7" x2="15" y2="7"/></g></svg>Notifications</span>
      <span class="nav-item" style="left:606px;top:33px">
        <svg viewBox="0 0 16 16"><circle cx="8" cy="8" r="7" fill="none" stroke="#5a4aa6" stroke-width="1.2"/><circle cx="8" cy="6.5" r="2.3" fill="none" stroke="#5a4aa6" stroke-width="1.2"/><path d="M3.8 12.5c1-2 2.5-3 4.2-3s3.2 1 4.2 3" fill="none" stroke="#5a4aa6" stroke-width="1.2"/></svg>Profile</span>
      <span class="nav-item" style="left:709px;top:33px">
        <svg viewBox="0 0 16 16"><circle cx="8" cy="8" r="5.5" fill="none" stroke="#1f3f66" stroke-width="1.6" stroke-dasharray="2 1.4"/><circle cx="8" cy="8" r="2.5" fill="none" stroke="#1f3f66" stroke-width="1.2"/></svg>Configuration</span>
    </nav>
  </header>

  <section class="hero" role="img" aria-label="Photo of a hand using a tablet showing business charts">
    <div class="stat" style="left:178px"><div class="stat-value" style="color:var(--hero-sky)">197</div><div class="stat-label">Number of active processes</div></div>
    <div class="stat-divider" style="left:241px"></div>
    <div class="stat" style="left:310px"><div class="stat-value" style="color:var(--hero-lilac)">124</div><div class="stat-label">Number of completed processes</div></div>
    <div class="stat-divider" style="left:386px"></div>
    <div class="stat" style="left:453px"><div class="stat-value" style="color:var(--hero-sky)">75%</div><div class="stat-label">Completion</div></div>
    <div class="stat-divider" style="left:522px"></div>
    <div class="stat feed" style="left:574px">
      <div class="avatar" role="img" aria-label="Profile photo of the latest activity author"></div>
      <div class="stat-label" style="margin-top:8px">Activity Feed</div>
      <div class="feed-name">Tomas Reyne</div>
      <div class="feed-date">March 30th | 2017</div>
    </div>
    <div class="stat-divider" style="left:630px"></div>
    <div class="stat" style="left:714px"><div class="stat-value" style="color:var(--hero-ice)">$2,627</div><div class="stat-label" style="margin-top:16px">Expenses</div></div>
    <div class="slider-dots"><span class="active"></span><span></span><span></span><span></span></div>
  </section>

  <article class="card blue" style="left:108px;top:540px"><div class="card-title">Process #1</div><div class="card-rule"></div><div class="card-heading">Process<br>Name</div><div class="card-value">Perspiciatis Unde</div></article>
  <article class="card violet" style="left:342px;top:540px"><div class="card-title">Process #2</div><div class="card-rule"></div><div class="card-heading">Cost</div><div class="card-value">$3,9735</div></article>
  <article class="card navy" style="left:578px;top:540px"><div class="card-title">Process #3</div><div class="card-rule"></div><div class="card-heading">Short<br>Description</div><div class="card-text">perspiciatis unde omnis iste natus error sit voluptatem accusantium</div></article>

  <article class="card blue" style="left:108px;top:830px"><div class="card-title">Process #n</div><div class="card-rule"></div><div class="card-heading">Completion<br>Stage</div><div class="card-count">1</div></article>
  <article class="card violet" style="left:342px;top:830px"><div class="card-title">+</div><div class="card-rule"></div><div class="card-heading">New<br>Process</div><div class="card-count">0</div></article>
  <article class="card navy" style="left:578px;top:830px">
    <div class="card-title"><svg width="12" height="14" viewBox="0 0 12 14"><rect x="0" y="2" width="12" height="1.6" fill="#fff"/><rect x="4" y="0" width="4" height="2" fill="#fff"/><path d="M1.5 4.5h9l-.8 9.5H2.3z" fill="#fff"/><g stroke="#1f3f66" stroke-width="1"><line x1="4.2" y1="6" x2="4.2" y2="12.5"/><line x1="6" y1="6" x2="6" y2="12.5"/><line x1="7.8" y1="6" x2="7.8" y2="12.5"/></g></svg></div>
    <div class="card-rule"></div><div class="card-heading">Deleted<br>Process</div><div class="card-count">0</div></article>

  <footer class="footer"><p>© 2017 Company Name &nbsp;|&nbsp; All Rihgts Reserved</p></footer>
</div>
</body>
</html>
```